PHGCCUL re-branding website and logo

We are looking for a new webpage design and logo our current page address is www.phgccul-example.org. We want to create a new design using PHGCCUL Pinewood and Harbour Growers Co-operative Credit Union limited and another with the purposed new name PHFC Pinewood and Harbour Financial Co-operative, the color scheme is purple and burnt orange. Our new logo and webpage should communicate change and growth purposed theme continuing our legacy here to server past, present and future generations. Our idea for the logo is a live shot of hands of different ages in a circle holding a tree

Target Market(s)

Everyone

Contact Information for Business Card

Company Name
Telephone number
Address
slot to enter employee info

Logo Text

(P & H) Pinewood And Harbour Financial Co-operative

Coding

Coded - Design and coding required

Number of Pages Required

2 page

Colors
f37122
fbed22
6b449b

Requirements
Must have
• links for social media

```html
<!DOCTYPE html>
<html lang="en">
<head>
<meta charset="utf-8">
<title>Pinewood and Harbour Financial Co-operative</title>
<link rel="stylesheet" href="https://fonts.googleapis.com/css2?family=Jost:wght@400;500;600&family=Lato:wght@400;700&display=swap">
<style>
:root{
  --purple:#6b449b;
  --orange:#f37122;
  --yellow:#fbed22;
  --ink:#222;
  --muted:#666;
  --grey-bg:#ebebed;
  --box-bg:#ebebeb;
  --line:#d6d6d6;
  --white:#fff;
}
*{margin:0;padding:0;box-sizing:border-box}
html,body{width:1200px;height:2332px;overflow:hidden;background:var(--white)}
body{font-family:"Lato",sans-serif;color:var(--ink)}
.page{position:relative;width:1200px;height:2332px;overflow:hidden}
.abs{position:absolute}
a{color:inherit;text-decoration:none}

/* top bar */
.topbar{left:0;top:0;width:1200px;height:47px;background:var(--purple)}
.topbar-rule{left:0;top:47px;width:1200px;height:4px;background:var(--orange)}
.toplinks{left:471px;top:0;height:47px;display:flex;align-items:center;font-family:"Jost",sans-serif;font-size:11px;color:var(--white);text-transform:uppercase}
.toplinks a{height:47px;display:flex;align-items:center;padding:0 14px;border-right:1px solid rgba(255,255,255,.25);gap:6px}
.toplinks a.active{background:var(--orange)}
.toplinks svg{width:11px;height:11px;fill:var(--white)}

/* brand */
.brand{display:flex;align-items:center;gap:14px}
.brand-dot{width:44px;height:44px;border-radius:50%;background:var(--purple);flex:none}
.brand-name{font-family:"Jost",sans-serif;font-weight:500;color:var(--purple);font-size:17px;line-height:22px}

/* main nav */
.mainnav{top:96px;font-family:"Jost",sans-serif;font-size:13px;font-weight:500;color:var(--ink);text-transform:uppercase;display:flex;align-items:center;gap:12px}
.mainnav svg{width:11px;height:8px;stroke:var(--ink);stroke-width:2;fill:none}

/* hero */
.hero{left:0;top:158px;width:1200px;height:543px;background:linear-gradient(180deg,#5f9bd9 0%,#b7d0e6 40%,#d7dde0 62%,#c7d27e 85%,#8fae2e 100%)}
.hero-photo{left:0;top:158px;width:640px;height:543px;background:radial-gradient(ellipse at 60% 62%,#e7b59a 0%,#d89d7f 30%,rgba(216,157,127,0) 62%)}
.hero-title{left:688px;top:270px;font-family:"Jost",sans-serif;font-weight:500;font-size:54px;line-height:68px;color:var(--purple);text-transform:uppercase;letter-spacing:1px}
.btn-orange{background:var(--orange);color:var(--white);font-family:"Jost",sans-serif;font-weight:500;text-transform:uppercase;display:flex;align-items:center;justify-content:center;gap:10px}
.hero-btn{left:698px;top:500px;width:171px;height:49px;font-size:17px}
.hero-btn svg{width:7px;height:11px;fill:var(--white)}
.hero-dots{left:533px;top:667px;width:135px;height:34px;background:var(--orange);display:flex;align-items:center;justify-content:center;gap:15px}
.hero-dots span{width:9px;height:9px;border-radius:50%;background:var(--white)}
.hero-dots span.on{width:12px;height:12px;background:none;border:2px solid var(--white)}

/* quick links */
.quick{top:747px;width:223px;height:66px;border:1.5px solid var(--purple);display:flex;align-items:center;gap:16px;padding-left:22px;font-family:"Jost",sans-serif;font-weight:600;font-size:14px;line-height:19px;color:var(--purple);text-transform:uppercase}
.quick svg{width:28px;height:28px;flex:none;stroke:var(--orange);fill:none;stroke-width:2}

/* notice */
.rule{height:1px;background:var(--line)}
.notice-art{left:132px;top:876px;width:320px;height:266px;background:linear-gradient(120deg,#1e8fc4 0%,#4aa83a 38%,#c8232a 62%,#a81d22 100%);border-radius:14px;opacity:.9}
.notice-title{left:516px;top:905px;font-family:"Jost",sans-serif;font-weight:600;font-size:30px;color:var(--orange);text-transform:uppercase}
.notice-body{left:516px;top:958px;width:540px;font-family:"Lato",sans-serif;font-size:17px;line-height:31px;color:var(--ink)}
.notice-btn{left:519px;top:1044px;width:214px;height:53px;background:var(--yellow);color:var(--purple);font-family:"Jost",sans-serif;font-weight:600;font-size:17px;display:flex;align-items:center;justify-content:center;text-transform:uppercase}

/* rates */
.section-title{font-family:"Jost",sans-serif;font-weight:600;font-size:27px;color:var(--orange);text-transform:uppercase}
.apr-note{left:698px;top:1232px;font-size:10px;color:var(--ink)}
.rates-btn{left:856px;top:1215px;width:210px;height:47px;background:var(--purple);color:var(--white);font-family:"Jost",sans-serif;font-weight:500;font-size:17px;display:flex;align-items:center;justify-content:center;gap:8px;text-transform:uppercase}
.rates-btn svg{width:14px;height:12px;stroke:var(--white);stroke-width:2;fill:none}
.rate{top:1293px;width:223px;height:189px;background:var(--box-bg);border:1px solid var(--line);text-align:center;font-family:"Jost",sans-serif}
.rate-value{margin-top:26px;font-size:40px;font-weight:400;color:var(--orange);line-height:50px}
.rate-apr{font-size:11px;color:var(--ink);padding-left:80px;line-height:14px}
.rate-name{margin-top:26px;font-size:19px;color:var(--purple)}
.rate-low{font-size:14px;color:var(--muted);margin-top:4px}

/* news */
.news-band{left:0;top:1552px;width:1200px;height:409px;background:var(--grey-bg)}
.news-arrows{left:1020px;top:1604px;display:flex;gap:16px}
.news-arrows svg{width:14px;height:22px;stroke:#777;stroke-width:2.5;fill:none}
.news-item{top:1690px;width:260px}
.news-date{display:inline-block;border:1px solid #aaa;font-size:9px;font-style:italic;color:#555;padding:2px 6px;background:var(--white)}
.news-head{margin-top:16px;width:240px;font-family:"Jost",sans-serif;font-weight:600;font-size:16px;line-height:24px;color:var(--purple);text-transform:uppercase}
.news-text{margin-top:16px;font-size:12px;line-height:21px;color:var(--muted);width:232px}
.news-more{margin-top:20px;width:88px;height:27px;font-size:11px}
.news-marker{top:1726px;width:25px;height:25px;background:var(--purple);display:flex;align-items:center;justify-content:center}
.news-marker svg{width:8px;height:11px;stroke:var(--white);stroke-width:2;fill:none}

/* footer */
.foot-col{top:2022px;width:220px}
.foot-head{font-family:"Jost",sans-serif;font-weight:600;font-size:13px;color:var(--purple);text-transform:uppercase;margin-bottom:18px}
.foot-row{display:flex;align-items:center;gap:12px;font-size:11px;color:var(--ink);height:32px}
.foot-row svg{width:10px;height:10px;fill:var(--purple);flex:none}
.foot-links{left:131px;top:2264px;font-size:10px;color:var(--ink)}
.foot-links span{padding:0 6px;border-left:1px solid #999}
.foot-links span:first-child{padding-left:0;border-left:none}
.copyright{right:132px;top:2264px;font-size:10px;color:var(--ink)}
</style>
</head>
<body>
<div class="page">

  <!-- top utility bar -->
  <div class="abs topbar"></div>
  <div class="abs topbar-rule"></div>
  <nav class="abs toplinks">
    <a class="active" href="#">Home</a>
    <a href="#">Apply for a loan</a>
    <a href="#">Become a member</a>
    <a href="#">Locations</a>
    <a href="#"><svg viewBox="0 0 24 24"><path d="M6.6 10.8a15 15 0 006.6 6.6l2.2-2.2a1 1 0 011-.25 11.4 11.4 0 003.6.6 1 1 0 011 1V20a1 1 0 01-1 1A17 17 0 013 4a1 1 0 011-1h3.5a1 1 0 011 1 11.4 11.4 0 00.6 3.6 1 1 0 01-.25 1z"/></svg>(242) 555-0140</a>
    <a href="#" style="border-right:none"><svg viewBox="0 0 24 24"><path d="M6 2h12v6H6zM3 9h18v9h-3v4H6v-4H3zM8 15v5h8v-5z"/></svg>(242) 555-0172</a>
  </nav>

  <!-- brand -->
  <div class="abs brand" style="left:132px;top:82px">
    <span class="brand-dot"></span>
    <span class="brand-name">Pinewood &amp; Harbour<br>Financial Co-operative</span>
  </div>

  <!-- main nav -->
  <div class="abs mainnav" style="left:471px">My Credit Union <svg viewBox="0 0 12 8"><path d="M1 1l5 5 5-5"/></svg></div>
  <div class="abs mainnav" style="left:676px">Products and Services <svg viewBox="0 0 12 8"><path d="M1 1l5 5 5-5"/></svg></div>
  <div class="abs mainnav" style="left:914px">Tools and Benefits <svg viewBox="0 0 12 8"><path d="M1 1l5 5 5-5"/></svg></div>

  <!-- hero -->
  <div class="abs hero"></div>
  <div class="abs hero-photo" role="img" aria-label="Photo of an open hand holding soil with a green seedling"></div>
  <h1 class="abs hero-title">Salaried<br>Financial<br>Co-operative</h1>
  <a class="abs btn-orange hero-btn" href="#">Learn more <svg viewBox="0 0 7 11"><path d="M0 0l7 5.5L0 11z"/></svg></a>
  <div class="abs hero-dots"><span></span><span class="on"></span><span></span><span></span><span></span></div>

  <!-- quick links -->
  <a class="abs quick" style="left:131px" href="#"><svg viewBox="0 0 28 28"><rect x="6" y="12" width="16" height="13" rx="1"/><path d="M9 12V8a5 5 0 0110 0v4"/><path d="M14 17v3"/></svg>Internet Teller<br>Login</a>
  <a class="abs quick" style="left:368px" href="#"><svg viewBox="0 0 28 28"><circle cx="14" cy="14" r="11"/><path d="M9 14l4 4 7-8"/></svg>Apply for a loan</a>
  <a class="abs quick" style="left:608px" href="#"><svg viewBox="0 0 28 28" style="fill:var(--orange);stroke:none"><circle cx="14" cy="8" r="5"/><path d="M5 26v-6a6 6 0 016-6h6a6 6 0 016 6v6z"/></svg>Become a member</a>
  <a class="abs quick" style="left:845px" href="#"><svg viewBox="0 0 28 28" style="stroke-width:1.6"><rect x="6" y="2" width="16" height="24" rx="1"/><rect x="9" y="5" width="10" height="5"/><path d="M9 14h2M13 14h2M17 14h2M9 18h2M13 18h2M17 18h2M9 22h2M13 22h2M17 22h2"/></svg>Financial<br>Calculators</a>

  <!-- notice -->
  <div class="abs rule" style="left:466px;top:873px;width:602px"></div>
  <div class="abs notice-art" role="img" aria-label="Illustration of three fanned bank cards in blue, green and red"></div>
  <h2 class="abs notice-title">ATM Cards Renewal Notice</h2>
  <p class="abs notice-body">Please be advised that all ATM Cards issued Febuary 2014, Expires Effective February 28,2017</p>
  <a class="abs notice-btn" href="#">Learn more here</a>
  <div class="abs rule" style="left:466px;top:1142px;width:602px"></div>

  <!-- featured rates -->
  <h2 class="abs section-title" style="left:131px;top:1218px">Featured Rates</h2>
  <div class="abs apr-note">APR* - Annual Percentage Rate.</div>
  <a class="abs rates-btn" href="#">Apply for a loan <svg viewBox="0 0 14 12"><path d="M1 1l5 5-5 5M7 1l5 5-5 5"/></svg></a>

  <div class="abs rate" style="left:131px"><div class="rate-value">9.00%</div><div class="rate-apr">APR*</div><div class="rate-name">Consumer Loans</div><div class="rate-low">as low as</div></div>
  <div class="abs rate" style="left:368px"><div class="rate-value">7.00%</div><div class="rate-apr">APR*</div><div class="rate-name">New Auto/Motorcycle</div><div class="rate-low">as low as</div></div>
  <div class="abs rate" style="left:608px"><div class="rate-value">11.75%</div><div class="rate-apr">APR*</div><div class="rate-name">Used Auto/Motorcycle</div><div class="rate-low">as low as</div></div>
  <div class="abs rate" style="left:845px"><div class="rate-value">8.25%</div><div class="rate-apr">APR*</div><div class="rate-name">Mortgage</div><div class="rate-low">as low as</div></div>

  <!-- news & events -->
  <div class="abs news-band"></div>
  <h2 class="abs section-title" style="left:131px;top:1596px">News &amp; Events</h2>
  <div class="abs news-arrows">
    <svg viewBox="0 0 14 22"><path d="M11 2L3 11l8 9"/></svg>
    <svg viewBox="0 0 14 22"><path d="M3 2l8 9-8 9"/></svg>
  </div>

  <div class="abs news-marker" style="left:123px"><svg viewBox="0 0 8 11"><path d="M1 1l5 4.5L1 10"/></svg></div>
  <article class="abs news-item" style="left:166px">
    <span class="news-date">March 10, 2017</span>
    <h3 class="news-head">Lorem Ipsum is simply dum and typesetting.</h3>
    <p class="news-text">It is a long established fact that a reader will be distracted by the readable content of a page when looking</p>
    <a class="btn-orange news-more" href="#">Read more</a>
  </article>

  <div class="abs news-marker" style="left:458px"><svg viewBox="0 0 8 11"><path d="M1 1l5 4.5L1 10"/></svg></div>
  <article class="abs news-item" style="left:502px">
    <span class="news-date">March 10, 2017</span>
    <h3 class="news-head">There are many variations of passages of Lorem</h3>
    <p class="news-text">All the Lorem Ipsum generators on the Internet tend to repeat predefined chunks as necessary, making this.</p>
    <a class="btn-orange news-more" href="#">Read more</a>
  </article>

  <div class="abs news-marker" style="left:805px"><svg viewBox="0 0 8 11"><path d="M1 1l5 4.5L1 10"/></svg></div>
  <article class="abs news-item" style="left:848px">
    <span class="news-date">March 10, 2017</span>
    <h3 class="news-head">On the other hand, we denounce with</h3>
    <p class="news-text">Choice is untrammelled and when nothing prevents our being able to do what we like best, every pleasure is to.</p>
    <a class="btn-orange news-more" href="#">Read more</a>
  </article>

  <!-- footer -->
  <div class="abs brand" style="left:132px;top:2085px">
    <span class="brand-dot"></span>
    <span class="brand-name">Pinewood &amp; Harbour<br>Financial Co-operative</span>
  </div>

  <div class="abs foot-col" style="left:432px">
    <div class="foot-head">Nassau</div>
    <div class="foot-row"><svg viewBox="0 0 10 10"><path d="M5 0a3.5 3.5 0 013.5 3.5C8.5 6 5 10 5 10S1.5 6 1.5 3.5A3.5 3.5 0 015 0zm0 2a1.5 1.5 0 100 3 1.5 1.5 0 000-3z"/></svg>Larch Street &amp; Harbour Dr.</div>
    <div class="foot-row"><svg viewBox="0 0 24 24"><path d="M6.6 10.8a15 15 0 006.6 6.6l2.2-2.2a1 1 0 011-.25 11.4 11.4 0 003.6.6 1 1 0 011 1V20a1 1 0 01-1 1A17 17 0 013 4a1 1 0 011-1h3.5a1 1 0 011 1 11.4 11.4 0 00.6 3.6 1 1 0 01-.25 1z"/></svg>(242) 555-0140</div>
    <div class="foot-row"><svg viewBox="0 0 24 24"><path d="M6 2h12v6H6zM3 9h18v9h-3v4H6v-4H3zM8 15v5h8v-5z"/></svg>(242) 555-0172</div>
  </div>
  <div class="abs foot-col" style="left:662px">
    <div class="foot-head">Freeport, Grand Bahama</div>
    <div class="foot-row"><svg viewBox="0 0 10 10"><path d="M5 0a3.5 3.5 0 013.5 3.5C8.5 6 5 10 5 10S1.5 6 1.5 3.5A3.5 3.5 0 015 0zm0 2a1.5 1.5 0 100 3 1.5 1.5 0 000-3z"/></svg>#8 West Cedar Dr.</div>
    <div class="foot-row"><svg viewBox="0 0 24 24"><path d="M6.6 10.8a15 15 0 006.6 6.6l2.2-2.2a1 1 0 011-.25 11.4 11.4 0 003.6.6 1 1 0 011 1V20a1 1 0 01-1 1A17 17 0 013 4a1 1 0 011-1h3.5a1 1 0 011 1 11.4 11.4 0 00.6 3.6 1 1 0 01-.25 1z"/></svg>(242) 555-0118</div>
    <div class="foot-row"><svg viewBox="0 0 24 24"><path d="M6 2h12v6H6zM3 9h18v9h-3v4H6v-4H3zM8 15v5h8v-5z"/></svg>(242) 555-0163</div>
  </div>
  <div class="abs foot-col" style="left:892px">
    <div class="foot-head">Abaco</div>
    <div class="foot-row"><svg viewBox="0 0 10 10"><path d="M5 0a3.5 3.5 0 013.5 3.5C8.5 6 5 10 5 10S1.5 6 1.5 3.5A3.5 3.5 0 015 0zm0 2a1.5 1.5 0 100 3 1.5 1.5 0 000-3z"/></svg>Bayview Plaza Shopping Centre</div>
    <div class="foot-row"><svg viewBox="0 0 24 24"><path d="M6.6 10.8a15 15 0 006.6 6.6l2.2-2.2a1 1 0 011-.25 11.4 11.4 0 003.6.6 1 1 0 011 1V20a1 1 0 01-1 1A17 17 0 013 4a1 1 0 011-1h3.5a1 1 0 011 1 11.4 11.4 0 00.6 3.6 1 1 0 01-.25 1z"/></svg>(242) 555-0191</div>
    <div class="foot-row"><svg viewBox="0 0 24 24"><path d="M6 2h12v6H6zM3 9h18v9h-3v4H6v-4H3zM8 15v5h8v-5z"/></svg>(242) 555-0127</div>
  </div>

  <div class="abs rule" style="left:131px;top:2225px;width:937px"></div>
  <div class="abs foot-links"><span>Privacy Policy</span><span>Website Terms</span><span>USA Patriot Act</span></div>
  <div class="abs copyright">Copyright © 2017 Pinewood &amp; Harbour Growers Co-operative Credit Union Ltd. All Rights Reserved.</div>

</div>
</body>
</html>
```